KDWB Business Card

Looking for a business card design to incorporate our branding. We want to only use the colors listing in the Branding Package (attached).
Updates

Target Market(s)

People who need their phone or device fixed.

Industry/Entity Type

Electronics

Contact Information for Business Card

Please use:

Brightwick Gadget Clinic LLC
4810 E Harlow Ridge Rd
Suite 417
San Antonio, TX 78163

Marcus Delgrove, Store Manager

(210) 555-0147

Requirements
Must have
• Must include the colors that are contained within the Branding Package PDF file.

```html
<!DOCTYPE html>
<html lang="en">
<head>
<meta charset="utf-8">
<title>Brightwick Gadget Clinic – Business Card</title>
<link href="https://fonts.googleapis.com/css2?family=Arimo:wght@400;700&display=swap" rel="stylesheet">
<style>
  :root {
    --orange: #e8542a;
    --graphite: #4b4d52;
    --ink: #3b3c40;
    --paper: #f7f7f7;
    --backdrop: #dcdcdc;
    --divider: #8a8b8f;
  }
  * { margin: 0; padding: 0; box-sizing: border-box; }
  html, body {
    width: 1200px; height: 902px; overflow: hidden;
    background: var(--backdrop);
    font-family: "Arimo", Arial, sans-serif;
  }
  .card {
    position: absolute; left: 100px; top: 165px;
    width: 1000px; height: 571px;
    background: var(--paper);
    box-shadow: 0 10px 30px rgba(0,0,0,0.18);
    overflow: hidden;
  }
  .card-bands { position: absolute; left: 0; top: 0; width: 1000px; height: 571px; }
  .brand {
    position: absolute; left: 70px; top: 215px;
    display: flex; align-items: center; gap: 16px;
  }
  .brand-mark { width: 58px; height: 58px; background: var(--orange); border-radius: 10px; }
  .brand-name {
    font-size: 40px; font-weight: 400; color: var(--orange);
    line-height: 1.05; width: 300px;
  }
  .divider {
    position: absolute; left: 495px; top: 40px;
    width: 2px; height: 380px; background: var(--divider);
  }
  .contact { position: absolute; left: 545px; top: 120px; color: var(--ink); }
  .contact-phone { display: flex; align-items: center; gap: 12px; font-size: 22px; }
  .contact-phone svg { width: 22px; height: 22px; }
  .contact-name { font-size: 33px; margin-top: 18px; }
  .contact-title { font-size: 19px; color: var(--orange); margin-top: 6px; }
  .address {
    position: absolute; left: 620px; top: 450px;
    display: flex; align-items: center; gap: 22px;
    color: #ffffff; font-size: 20px; line-height: 1.35;
  }
  .address svg { width: 20px; height: 24px; }
</style>
</head>
<body>
  <div class="card">
    <svg class="card-bands" viewBox="0 0 1000 571" aria-hidden="true">
      <path fill="var(--graphite)" d="M0 490 L1000 380 L1000 571 L0 571 Z"/>
      <path fill="var(--orange)" d="M600 440 Q588 442 586 460 L586 571 L1000 571 L1000 395 Z"/>
    </svg>

    <div class="brand">
      <div class="brand-mark"></div>
      <div class="brand-name">Brightwick Gadget Clinic</div>
    </div>

    <div class="divider"></div>

    <div class="contact">
      <div class="contact-phone">
        <svg viewBox="0 0 22 22" aria-hidden="true">
          <rect width="22" height="22" fill="var(--orange)"/>
          <path fill="#fff" d="M7 5 L9.5 5 L10.5 8 L9 9.3 Q10.5 12.5 13 13.5 L14.3 12 L17 13 L17 15.5 Q16.5 17 15 17 Q6 15.5 5 7 Q5 5.5 7 5 Z"/>
        </svg>
        <span>(210) 555-0147</span>
      </div>
      <div class="contact-name">Marcus Delgrove</div>
      <div class="contact-title">Store Manager</div>
    </div>

    <div class="address">
      <svg viewBox="0 0 20 24" aria-hidden="true">
        <rect width="20" height="24" fill="#fff"/>
        <path fill="var(--orange)" d="M10 4 A5 5 0 0 1 15 9 Q15 12 10 19 Q5 12 5 9 A5 5 0 0 1 10 4 Z"/>
        <circle cx="10" cy="9" r="2" fill="#fff"/>
      </svg>
      <div>
        <div>4810 E Harlow Ridge Rd</div>
        <div>Suite 417, San Antonio, TX 78163</div>
      </div>
    </div>
  </div>
</body>
</html>
```